banner for website

I need a new banner for my website. My website now is. www.brightmeadowkitchen.com, but I'm changing it to Bright Meadow Table and I need a new banner. I want me to be who it's about. I am my brand. I'm Carla Whitford. So, my name needs to be prominent in the banner along with my photo, which I'm attaching. I want my photo very prominent in the banner and very large. I am attaching my two favorites.
I need the banner plain ( with out the newsletter sign up optin part), so I can use it on my newsletters, emails and letter head, as well. I would like it to be inviting. I I have a certain color scheme I use. Deep dark brown letters with blues and greens. Very earthy and psychologically grounded. I would like to keep that color scheme. In my website banner, I need a opt in to sign up for my free monthly newsletter and receive my Free Pantry Basket Planner.

I want the shopping guide to be small and pleasant looking and to say: "Sign up to receive your Free Pantry Basket Planner and monthly newsletter."

I only want my banner to say: "Bright Meadow Table" "Carla Whitford"

I would also like to have part of the banner without the sign in for the newsletter part off of it. And also one with only the "Bright Meadow Table" and one with "Bright Meadow Table" and "Carla Whitford" without the newsletter sign up part on it either.

I hope you can do this for me. I look forward to seeing your design! Sincerely, Carla
Updates

Project Deadline Extended Reason: I couldn't view the designs so I couldn't look at the ones submitted. I just now got into the website with your company's help. I don't want to be penalized because of a problem with the log in at your site. That was not my fault. Please let me know your thoughts. Added Monday, May 9, 2016

Target Market(s)

people over 40 who have bad health or who want to learn how to be a vegetarian for better health.

Number of Pages Required

1 page

Requirements
Must have
• I want the shopping guide to be small and pleasant looking and to say: "Sign up to receive your Free Pantry Basket Planner and monthly newsletter." I would like it to blend and be elegant and not in the middle of the banner or across my face.
• I only want my banner to say: "Bright Meadow Table" "Carla Whitford"
• I would also like to have part of the banner without the sign in for the newsletter part off of it. And also one with only the "Bright Meadow Table" and one with "Bright Meadow Table" and "Carla Whitford" without the newsletter sign up part on it either.
Nice to have
• Nice font and colors. I want the background to be plants and earthy and inviting.
Should not have
• I updated and added two new photos. I think the one you were using with me in the red top looked funny under my eyes. it was too pink or something. I uploaded a better version of that photo. in hopes that it looks better. Please switch those out if you are using the one with me in the red top.

```html
<!DOCTYPE html>
<html lang="en">
<head>
<meta charset="utf-8">
<title>Carla Whitford · Bright Meadow Table</title>
<link rel="stylesheet" href="https://fonts.googleapis.com/css2?family=Raleway:wght@400;500&display=swap">
<style>
  :root {
    --brown-deep: #4a1d0b;
    --leaf-green: #5f9a1f;
    --band-green: #7db52b;
    --mist-white: #f6fbfb;
    --sky-blue: #cfeaf0;
    --aqua: #4fc3c0;
    --teal-deep: #1f8a86;
    --sage-light: #a9b59c;
    --sage-deep: #5f7d4a;
    --white: #ffffff;
  }
  * { box-sizing: border-box; margin: 0; padding: 0; }
  html, body { width: 1200px; height: 510px; overflow: hidden; background: var(--white); }
  .banner {
    position: relative;
    width: 1200px;
    height: 510px;
    overflow: hidden;
    font-family: "Raleway", "Helvetica Neue", Arial, sans-serif;
  }
  .banner__backdrop {
    position: absolute;
    inset: 0 0 61px 0;
    background:
      radial-gradient(ellipse 260px 200px at 60px 60px, rgba(124, 204, 58, 0.75), rgba(124, 204, 58, 0) 70%),
      radial-gradient(ellipse 220px 180px at 560px 120px, rgba(158, 220, 70, 0.7), rgba(158, 220, 70, 0) 70%),
      radial-gradient(ellipse 330px 300px at 1120px 220px, rgba(31, 138, 134, 0.9), rgba(31, 138, 134, 0) 75%),
      radial-gradient(ellipse 260px 200px at 900px 440px, rgba(124, 204, 58, 0.85), rgba(124, 204, 58, 0) 70%),
      linear-gradient(100deg, var(--mist-white) 0%, var(--mist-white) 30%, var(--sky-blue) 50%, var(--aqua) 72%, var(--teal-deep) 100%);
  }
  .identity {
    position: absolute;
    left: 91px;
    top: 183px;
  }
  .identity__name {
    font-weight: 400;
    font-size: 53px;
    line-height: 1;
    letter-spacing: 0.5px;
    color: var(--brown-deep);
    text-transform: uppercase;
    white-space: nowrap;
  }
  .identity__tagline {
    margin-top: 18px;
    font-weight: 400;
    font-size: 34px;
    line-height: 1;
    color: var(--leaf-green);
    text-transform: uppercase;
    white-space: nowrap;
  }
  .portrait {
    position: absolute;
    left: 681px;
    top: 18px;
    width: 406px;
    height: 406px;
    border-radius: 50%;
    border: 7px solid var(--white);
    background: linear-gradient(165deg, var(--sage-light) 0%, var(--sage-deep) 100%);
  }
  .signup-band {
    position: absolute;
    left: 0;
    bottom: 0;
    width: 1200px;
    height: 61px;
    background: var(--band-green);
  }
  .signup-band__text {
    position: absolute;
    left: 94px;
    top: 50%;
    transform: translateY(-50%);
    font-size: 21px;
    font-weight: 400;
    color: var(--white);
    white-space: nowrap;
  }
  .signup-band__button {
    position: absolute;
    left: 971px;
    top: 13px;
    width: 116px;
    height: 37px;
    border: 2px solid var(--white);
    display: flex;
    align-items: center;
    justify-content: center;
    font-size: 16px;
    font-weight: 500;
    color: var(--white);
    text-transform: uppercase;
    letter-spacing: 0.5px;
  }
</style>
</head>
<body>
  <div class="banner">
    <div class="banner__backdrop" role="img" aria-label="Soft watercolour backdrop of fresh green leaves on a misty white, aqua and teal wash"></div>

    <div class="identity">
      <h1 class="identity__name">Carla Whitford</h1>
      <p class="identity__tagline">For Bright Meadow Table</p>
    </div>

    <div class="portrait" role="img" aria-label="Round portrait photo of Carla holding fresh greens and potted herbs at a garden nursery"></div>

    <div class="signup-band">
      <p class="signup-band__text">Sign up for my free monthly newsletter and receive my free pantry basket planner</p>
      <span class="signup-band__button">Sign up</span>
    </div>
  </div>
</body>
</html>
```